Boutique custom software development company needs new business card

Our nearly 20 year old custom software development company would like to better include the fact that we are now providing Bitcoin services. These new services are B2B include education (how to acquire and securely hold Bitcoin) and integrating Bitcoin payments into existing ecommerce sites or other existing systems. Please keep the card clean and simple. Attached is our current design and some other files. vextorial.com

Target Market(s)

businesses owners interested in long term relationship

Industry/Entity Type

Custom software development and Bitcoin

Contact Information for Business Card

Dale Parker, dale@vextorial.com, vextorial.com, (888) 555-VXTRL

Font styles to use
Other font styles liked:
• monospace

Requirements
Must have
• double-sided
Nice to have
• clean and simple
Should not have
• physical address

```html
<!DOCTYPE html>
<html lang="en">
<head>
<meta charset="utf-8">
<title>Vextorial Business Card</title>
<link href="https://fonts.googleapis.com/css2?family=Montserrat:wght@700;800&family=Open+Sans:wght@400;600&display=swap" rel="stylesheet">
<style>
  :root {
    --brand-blue: #3d72b9;
    --brand-orange: #f07c22;
    --paper: #ffffff;
    --backdrop: #d6d6d6;
    --shadow: rgba(0, 0, 0, 0.22);
  }
  * { box-sizing: border-box; margin: 0; padding: 0; }
  html, body {
    width: 1200px; height: 800px; overflow: hidden;
    background: var(--backdrop);
  }
  .canvas {
    width: 1200px; height: 800px;
    display: flex; flex-direction: column;
    align-items: center; justify-content: center; gap: 60px;
  }
  .card {
    position: relative;
    width: 525px; height: 300px;
    border-radius: 22px;
    overflow: hidden;
    box-shadow: 0 12px 28px var(--shadow);
  }

  /* Front side */
  .card--front { background: var(--paper); }
  .brand {
    position: absolute; left: 190px; top: 34px;
  }
  .brand__name {
    font-family: "Montserrat", sans-serif; font-weight: 800;
    font-size: 38px; letter-spacing: 1px; line-height: 1;
    color: var(--brand-blue);
  }
  .brand__tagline {
    font-family: "Open Sans", sans-serif; font-weight: 400;
    font-size: 13.5px; line-height: 1.3; color: var(--brand-blue);
    margin-top: 4px; margin-left: 4px; white-space: nowrap;
  }
  .accent-orange {
    position: absolute; right: 0; top: 112px;
    width: 118px; height: 70px; background: var(--brand-orange);
  }
  .accent-blue {
    position: absolute; left: 330px; top: 150px;
    width: 82px; height: 82px; background: var(--brand-blue);
  }
  .contact-band {
    position: absolute; left: 0; top: 176px;
    width: 318px; height: 92px; background: var(--brand-blue);
    padding: 12px 0 0 30px;
  }
  .holder-name {
    position: absolute; left: 30px; top: 142px;
    font-family: "Montserrat", sans-serif; font-weight: 800;
    font-size: 22px; line-height: 1.2; letter-spacing: 0.5px; text-transform: uppercase;
  }
  .holder-name__first { color: var(--brand-orange); }
  .holder-name__last { color: var(--brand-blue); }
  .contact-list { list-style: none; }
  .contact-list__item {
    display: flex; align-items: center; gap: 10px;
    font-family: "Open Sans", sans-serif; font-size: 14px;
    color: var(--paper); height: 23px;
  }
  .contact-icon {
    width: 18px; height: 18px; border-radius: 3px;
    background: var(--paper);
    display: flex; align-items: center; justify-content: center;
  }

  /* Back side */
  .card--back {
    background: var(--brand-blue);
    display: flex; flex-direction: column;
    align-items: center; justify-content: center;
  }
  .card--back .brand__name { color: var(--paper); font-size: 62px; }
  .card--back .brand__tagline { color: var(--paper); font-size: 21px; margin-top: 6px; margin-left: 0; }
</style>
</head>
<body>
<main class="canvas">

  <section class="card card--front" aria-label="Business card front">
    <div class="brand">
      <div class="brand__name">VEXTORIAL</div>
      <div class="brand__tagline">custom software &amp; Bitcoin services</div>
    </div>
    <div class="accent-orange"></div>
    <div class="accent-blue"></div>

    <h1 class="holder-name"><span class="holder-name__first">Dale</span> <span class="holder-name__last">Parker</span></h1>

    <div class="contact-band">
      <ul class="contact-list">
        <li class="contact-list__item">
          <span class="contact-icon">
            <svg width="12" height="12" viewBox="0 0 24 24"><path fill="#f07c22" d="M6.6 10.8a15 15 0 0 0 6.6 6.6l2.2-2.2c.3-.3.7-.4 1-.2 1.1.4 2.3.6 3.6.6.6 0 1 .4 1 1V20c0 .6-.4 1-1 1A17 17 0 0 1 3 4c0-.6.4-1 1-1h3.5c.6 0 1 .4 1 1 0 1.3.2 2.5.6 3.6.1.3 0 .7-.2 1z"/></svg>
          </span>
          (888) 555-VXTRL
        </li>
        <li class="contact-list__item">
          <span class="contact-icon">
            <svg width="12" height="12" viewBox="0 0 24 24"><rect x="2" y="5" width="20" height="14" fill="#f07c22"/><path d="M2 5l10 8 10-8" fill="none" stroke="#fff" stroke-width="2"/></svg>
          </span>
          dale@vextorial.com
        </li>
        <li class="contact-list__item">
          <span class="contact-icon">
            <svg width="12" height="12" viewBox="0 0 24 24" fill="none" stroke="#f07c22" stroke-width="2"><circle cx="12" cy="12" r="10"/><ellipse cx="12" cy="12" rx="4" ry="10"/><path d="M2 12h20"/></svg>
          </span>
          www.vextorial.com
        </li>
      </ul>
    </div>
  </section>

  <section class="card card--back" aria-label="Business card back">
    <div class="brand__name">VEXTORIAL</div>
    <div class="brand__tagline">custom software &amp; Bitcoin services</div>
  </section>

</main>
</body>
</html>
```